Business Card Design Competition

We need a business card design for our Internet Marketing company. We require both front and back designs and the final card must be 89x53mm in size, plus crop marks to 91x55mm. Colours as per logo, plus perhaps black and/or grey (#828282).
Final text must be editable (if you can supply an editable Fireworks PNG, even better)...
FRONT TEXT:
Full Name
Position
Address Line
Suburb, State, Postcode
Phone: 0000 000 000
Mobile: 0000 000 000
Email: xxx@brightlanemedia.com.au
Web: www.brightlanemedia.com.au
Rear of card should be a fresh design plus our slogan text: "Helping You Stand Out" in large font, then in small text "Kestrel Holdings Pty Ltd (ABN: 42 561 903 774)".
Target Market(s)
Small/Medium Businesses
Industry/Entity Type
Business

```html
<!DOCTYPE html>
<html lang="en">
<head>
<meta charset="utf-8">
<title>Brightlane Media – Business Cards</title>
<link rel="stylesheet" href="https://fonts.googleapis.com/css2?family=Exo+2:wght@400;500&family=Open+Sans:wght@400;700&display=swap">
<style>
  :root {
    --stage: #e9e7e3;
    --card-dark: #2a2a2a;
    --card-dark-edge: #1f1f1f;
    --card-light: #ffffff;
    --green: #8cc63f;
    --orange: #f7941d;
    --grey: #828282;
    --ink-dark: #333333;
    --ink-light: #f2f2f2;
  }
  * { box-sizing: border-box; margin: 0; padding: 0; }
  html, body { width: 1200px; height: 900px; overflow: hidden; }
  body {
    background: var(--stage);
    position: relative;
    font-family: "Open Sans", Arial, sans-serif;
  }
  .card {
    position: absolute;
    width: 546px;
    height: 307px;
    border-radius: 18px;
    overflow: hidden;
  }
  .card--dark { background: linear-gradient(90deg, var(--card-dark-edge), var(--card-dark) 60%, #303030); color: var(--ink-light); }
  .card--light { background: var(--card-light); color: var(--ink-dark); }
  .card--front.card--dark { border-bottom: 10px solid var(--green); }
  .card--front.card--light { border-bottom: 10px solid #9a9a9a; }
  .pos-tl { left: 36px; top: 150px; }
  .pos-tr { left: 620px; top: 150px; }
  .pos-bl { left: 36px; top: 488px; }
  .pos-br { left: 620px; top: 488px; }

  /* front */
  .person { position: absolute; left: 34px; top: 56px; }
  .person__name { font-weight: 700; font-size: 17px; line-height: 1.1; }
  .card--light .person__name { color: var(--green); }
  .person__role { font-size: 10.5px; }
  .address { position: absolute; left: 34px; top: 124px; font-size: 11px; line-height: 1.45; }
  .contact-list { position: absolute; left: 34px; list-style: none; font-size: 11px; line-height: 1.45; }
  .contact-list--phone { top: 162px; }
  .contact-list--web { top: 207px; }
  .contact-list li { display: flex; align-items: center; gap: 8px; }
  .contact-list svg { width: 10px; height: 10px; flex: none; }
  .card--light .contact-list svg { color: var(--green); }
  .brand-mark { position: absolute; left: 272px; top: 115px; display: flex; align-items: center; gap: 10px; }
  .brand-mark__dot { width: 46px; height: 46px; border-radius: 50%; background: var(--orange); flex: none; }
  .brand-mark__name { font-family: "Exo 2", Arial, sans-serif; font-weight: 500; font-size: 24px; color: var(--green); white-space: nowrap; }

  /* back */
  .feature-circle { position: absolute; left: 322px; top: -12px; width: 330px; height: 330px; border-radius: 50%; background: var(--orange); }
  .card--dark .feature-circle { box-shadow: -14px 0 0 0 var(--card-dark), -24px 0 0 0 var(--green); }
  .card--light .feature-circle { box-shadow: -14px 0 0 0 var(--card-light), -24px 0 0 0 var(--green); }
  .back-name { position: absolute; left: 28px; top: 82px; font-family: "Exo 2", Arial, sans-serif; font-weight: 500; font-size: 40px; line-height: 1.05; color: var(--orange); }
  .slogan { position: absolute; left: 28px; top: 172px; font-family: "Exo 2", Arial, sans-serif; font-size: 17px; letter-spacing: 2px; white-space: nowrap; }
  .card--light .slogan { color: var(--grey); }
  .legal { position: absolute; left: 28px; font-size: 10px; white-space: nowrap; }
  .card--dark .legal { top: 272px; }
  .card--light .legal { top: 204px; color: var(--grey); }
</style>
</head>
<body>

<section class="card card--dark card--front pos-tl">
  <div class="person">
    <p class="person__name">Elena Hartwell</p>
    <p class="person__role">Company Director</p>
  </div>
  <p class="address">17 harbour view lane, Westbrook<br>Northvale WB12 3KL 5678</p>
  <ul class="contact-list contact-list--phone">
    <li><svg viewBox="0 0 10 10"><rect x="2.5" y="0.5" width="5" height="9" rx="1" fill="currentColor"/></svg>061-700-4821</li>
    <li><svg viewBox="0 0 10 10"><path d="M1 3c0-2 2-2 8 0v2H7V4H3v1H1z M2 6h6l1 3H1z" fill="currentColor"/></svg>061-704-9136</li>
  </ul>
  <ul class="contact-list contact-list--web">
    <li><svg viewBox="0 0 10 10"><rect x="0.5" y="1.5" width="9" height="7" fill="none" stroke="currentColor"/><path d="M0.5 1.5 5 5.5 9.5 1.5" fill="none" stroke="currentColor"/></svg>elena@brightlanemedia.com.au</li>
    <li><svg viewBox="0 0 10 10"><circle cx="5" cy="5" r="4.3" fill="none" stroke="currentColor"/><ellipse cx="5" cy="5" rx="2" ry="4.3" fill="none" stroke="currentColor"/><path d="M0.7 5h8.6" stroke="currentColor"/></svg>brightlanemedia.com.au</li>
  </ul>
  <div class="brand-mark"><span class="brand-mark__dot"></span><span class="brand-mark__name">Brightlane Media</span></div>
</section>

<section class="card card--dark card--back pos-tr">
  <div class="feature-circle"></div>
  <p class="back-name">Brightlane<br>Media</p>
  <p class="slogan">Helping You Stand Out</p>
  <p class="legal">Kestrel Holdings Pty Ltd (ABN: 42 561 903 774)</p>
</section>

<section class="card card--light card--front pos-bl">
  <div class="person">
    <p class="person__name">Elena Hartwell</p>
    <p class="person__role">Company Director</p>
  </div>
  <p class="address">17 harbour view lane, Westbrook<br>Northvale WB12 3KL 5678</p>
  <ul class="contact-list contact-list--phone">
    <li><svg viewBox="0 0 10 10"><rect x="2.5" y="0.5" width="5" height="9" rx="1" fill="currentColor"/></svg>061-700-4821</li>
    <li><svg viewBox="0 0 10 10"><path d="M1 3c0-2 2-2 8 0v2H7V4H3v1H1z M2 6h6l1 3H1z" fill="currentColor"/></svg>061-704-9136</li>
  </ul>
  <ul class="contact-list contact-list--web">
    <li><svg viewBox="0 0 10 10"><rect x="0.5" y="1.5" width="9" height="7" fill="none" stroke="currentColor"/><path d="M0.5 1.5 5 5.5 9.5 1.5" fill="none" stroke="currentColor"/></svg>elena@brightlanemedia.com.au</li>
    <li><svg viewBox="0 0 10 10"><circle cx="5" cy="5" r="4.3" fill="none" stroke="currentColor"/><ellipse cx="5" cy="5" rx="2" ry="4.3" fill="none" stroke="currentColor"/><path d="M0.7 5h8.6" stroke="currentColor"/></svg>brightlanemedia.com.au</li>
  </ul>
  <div class="brand-mark"><span class="brand-mark__dot"></span><span class="brand-mark__name">Brightlane Media</span></div>
</section>

<section class="card card--light card--back pos-br">
  <div class="feature-circle"></div>
  <p class="back-name">Brightlane<br>Media</p>
  <p class="slogan">Helping You Stand Out</p>
  <p class="legal">Kestrel Holdings Pty Ltd (ABN: 42 561 903 774)</p>
</section>

</body>
</html>
```